Harborline Auto LLC

Car Dealer Customer Service
Address: 2874 Cresthaven Road, Shelbyville, TN 37162
web: www.harborlineautoxq.net
email: harborlineautoxq@mailnest.example
Phone: (931) 555-0148
Phone: (629) 555-0173

```html
<!DOCTYPE html>
<html lang="en">
<head>
<meta charset="utf-8">
<title>Harborline Auto – Business Card</title>
<link rel="stylesheet" href="https://fonts.googleapis.com/css2?family=Lexend:wght@700&family=Poppins:wght@400;600&family=Nunito:wght@800&display=swap">
<style>
  :root {
    --page: #2b2b2b;
    --blue: #1f7db3;
    --blue-deep: #17618f;
    --blue-text: #1c6a9c;
    --gold: #dca23c;
    --paper: #f1f1f0;
    --ink: #1e1e1e;
    --white: #ffffff;
  }
  * { margin: 0; padding: 0; box-sizing: border-box; }
  html, body { width: 1200px; height: 1138px; overflow: hidden; background: var(--page); }
  .card {
    position: absolute;
    width: 620px;
    height: 376px;
    border-radius: 16px;
    overflow: hidden;
  }
  .card--front {
    left: 274px; top: 186px;
    background: linear-gradient(135deg, var(--blue-deep) 0%, var(--blue) 70%, #2286c0 100%);
  }
  .card--back {
    left: 276px; top: 608px;
    background: var(--paper);
  }
  .brand-name {
    position: absolute;
    font-family: "Lexend", sans-serif;
    font-weight: 700;
    font-size: 28px;
    letter-spacing: 0.5px;
    white-space: nowrap;
  }
  .card--front .brand-name { right: 42px; top: 56px; color: var(--white); }
  .card--back .brand-name { left: 28px; top: 42px; color: var(--blue-text); }
  .brand-disc {
    position: absolute;
    border-radius: 50%;
  }
  .card--front .brand-disc {
    width: 344px; height: 344px; left: -54px; top: 16px;
    background: var(--white);
  }
  .card--back .brand-disc {
    width: 384px; height: 384px; left: 332px; top: -16px;
    background: linear-gradient(160deg, #2384bd, var(--blue-deep));
  }
  .front-web {
    position: absolute; right: 42px; bottom: 34px;
    font-family: "Poppins", sans-serif; font-size: 15px; color: var(--white);
  }
  .person { position: absolute; left: 28px; top: 150px; }
  .person-name {
    font-family: "Nunito", sans-serif; font-weight: 800;
    font-size: 23px; color: var(--blue-text); line-height: 1.2;
  }
  .person-role {
    font-family: "Poppins", sans-serif; font-size: 15px; color: var(--ink);
  }
  .contacts {
    position: absolute; left: 28px; top: 228px;
    font-family: "Poppins", sans-serif; list-style: none;
  }
  .contact { display: flex; align-items: center; gap: 10px; height: 22.5px; font-size: 15px; color: var(--ink); }
  .contact--phone { font-weight: 600; font-size: 16px; color: var(--blue-text); letter-spacing: 0.4px; }
  .contact svg { width: 16px; height: 14px; fill: var(--gold); flex: none; }
  .address {
    position: absolute; left: 28px; top: 324px;
    font-family: "Poppins", sans-serif; font-size: 15px; color: var(--ink);
  }
</style>
</head>
<body>

<section class="card card--front">
  <div class="brand-disc" aria-hidden="true"></div>
  <p class="brand-name">HARBORLINE AUTO</p>
  <p class="front-web">www.harborlineautoxq.net</p>
</section>

<section class="card card--back">
  <div class="brand-disc" aria-hidden="true"></div>
  <p class="brand-name">HARBORLINE AUTO</p>

  <div class="person">
    <p class="person-name">Corin Vale</p>
    <p class="person-role">Managing Director</p>
  </div>

  <ul class="contacts">
    <li class="contact contact--phone">
      <svg viewBox="0 0 16 14"><path d="M2 4c0-2 2-3 6-3s6 1 6 3v1h-3V4H5v1H2zM4 6h8l2 7H2z"/></svg>
      931-555-0148
    </li>
    <li class="contact contact--phone">
      <svg viewBox="0 0 16 14"><path d="M2 4c0-2 2-3 6-3s6 1 6 3v1h-3V4H5v1H2zM4 6h8l2 7H2z"/></svg>
      629-555-0173
    </li>
    <li class="contact">
      <svg viewBox="0 0 16 14"><path d="M1 2h14v10H1zM2 3l6 5 6-5v1L8 9 2 4z" fill-rule="evenodd"/></svg>
      www.harborlineautoxq.net
    </li>
    <li class="contact">
      <svg viewBox="0 0 16 14"><circle cx="8" cy="7" r="6" fill="none" stroke="#dca23c" stroke-width="1.4"/><path d="M2 7h12M8 1v12" stroke="#dca23c" stroke-width="1.2"/></svg>
      harborlineautoxq@mailnest.example
    </li>
  </ul>

  <p class="address">2874 Cresthaven Road, Shelbyville, TN 37162</p>
</section>

</body>
</html>
```